I need to make a car magnet

It needs to include the words "PLAVO TOUR" and "2026 MEMBER" as well as the attached silhouette of the golfer. The color scheme needs to be navy, red and white. The shape and dimensions are open for interpretation

```html
<!DOCTYPE html>
<html lang="en">
<head>
<meta charset="utf-8">
<title>PLAVO TOUR – Car Magnet</title>
<link rel="stylesheet" href="https://fonts.googleapis.com/css2?family=Exo+2:ital,wght@1,800;1,900&display=swap">
<style>
  :root {
    --backdrop: #b3b3b3;
    --navy: #1e2b5b;
    --red: #e52431;
    --white: #ffffff;
  }
  * { margin: 0; padding: 0; box-sizing: border-box; }
  html, body {
    width: 892px;
    height: 1200px;
    overflow: hidden;
    background: var(--backdrop);
  }
  .magnet {
    position: absolute;
    left: 46px;
    top: 400px;
    width: 800px;
    height: 400px;
    background: var(--white);
    box-shadow: 2px 3px 6px rgba(0, 0, 0, 0.35);
    overflow: hidden;
  }
  .member-band {
    position: absolute;
    left: 186px;
    top: 293px;
    width: 614px;
    height: 55px;
    background: var(--navy);
  }
  .golfer-art {
    position: absolute;
    left: 0;
    top: 0;
    width: 226px;
    height: 400px;
    background: linear-gradient(90deg, var(--navy) 0%, var(--navy) 30%, #e9ecf4 62%, var(--white) 100%);
  }
  .wordmark {
    position: absolute;
    left: 226px;
    right: 0;
    top: 56px;
    text-align: center;
    font-family: "Exo 2", sans-serif;
    font-style: italic;
    font-weight: 900;
    line-height: 0.96;
    letter-spacing: 1px;
  }
  .wordmark .line-top {
    display: block;
    color: var(--red);
    font-size: 104px;
    padding-left: 20px;
  }
  .wordmark .line-bottom {
    display: block;
    color: var(--navy);
    font-size: 104px;
    padding-left: 0;
  }
  .member-label {
    position: absolute;
    left: 226px;
    right: 0;
    top: 293px;
    height: 55px;
    display: flex;
    align-items: center;
    justify-content: center;
    padding-right: 20px;
    font-family: "Exo 2", sans-serif;
    font-style: italic;
    font-weight: 800;
    font-size: 38px;
    letter-spacing: 1px;
    color: var(--white);
  }
</style>
</head>
<body>
  <div class="magnet">
    <div class="member-band"></div>
    <div class="golfer-art" role="img" aria-label="White silhouette of a golfer putting, outlined in navy, set against a navy panel"></div>
    <h1 class="wordmark">
      <span class="line-top">PLAVO</span>
      <span class="line-bottom">TOUR</span>
    </h1>
    <p class="member-label">2026 MEMBER</p>
  </div>
</body>
</html>
```